13 Varno - new website design project

Our company Varno Electrical is developing a new lead generation website focused on Electrical, LED Lighting and Solar Power. We need a high converting website.

Example of our current website is www.varnoelectrical-example.com.au You can take content from this website for this new design. Our colours are red, black and white. For our new website we would like to promote Varno, Spark Every Day. Please listen to the jingle.

The below link is the company jingle that we have developed.
http://www.tunecraftdemo.com.au/vrn-tc-v1/

The key for this brief is to generate leads for Electrical, LED Lighting (for commercial) and Solar Power & Storage.

Target Market(s)

Business owners in Melbourne Victoria

Number of Pages Required

4 page

Colors
ec1f27
ffffff

Requirements
Must have
• This page must be clean, be in line with company branding and a high converting lead website.

```html
<!DOCTYPE html>
<html lang="en">
<head>
<meta charset="utf-8">
<title>Varno Electrical</title>
<link href="https://fonts.googleapis.com/css2?family=Exo+2:wght@400;500;600&family=Lato:wght@400;700&display=swap" rel="stylesheet">
<style>
:root{
  --red:#ec1f27;
  --red-deep:#d0282d;
  --black:#111111;
  --charcoal:#2b2b2b;
  --white:#ffffff;
  --text:#333333;
}
*{margin:0;padding:0;box-sizing:border-box}
html,body{width:1200px;height:3056px;overflow:hidden;background:var(--white)}
body{position:relative;font-family:"Lato",sans-serif;color:var(--text)}
h2,h3{font-weight:400}
.abs{position:absolute}

/* top bar */
.topbar{left:0;top:0;width:1200px;height:45px;background:var(--red)}
.top-item{top:0;height:45px;display:flex;align-items:center;gap:10px;color:var(--white);font-size:14px;white-space:nowrap}
.search{left:966px;top:6px;width:164px;height:33px;border-left:1px solid rgba(255,255,255,.6);display:flex;align-items:center;justify-content:space-between;padding:0 12px;color:var(--white);font-size:14px}

/* header */
.brand{left:77px;top:68px;display:flex;align-items:center;gap:14px}
.brand .mark{width:30px;height:30px;background:var(--red)}
.brand .name{font-family:"Exo 2",sans-serif;font-weight:600;font-size:30px;color:var(--black);letter-spacing:1px}
.nav{top:69px;height:45px;display:flex;align-items:center;font-family:"Exo 2",sans-serif;font-size:18px;color:var(--black);letter-spacing:.5px}
.nav.active{border:2px solid var(--red);justify-content:center;width:107px}

/* hero */
.hero{left:0;top:143px;width:1200px;height:570px;background:linear-gradient(110deg,#2c3442 0%,#56606f 40%,#c9a56a 62%,#e8e6e0 100%)}
.bokeh{left:0;top:713px;width:1200px;height:469px;background:radial-gradient(circle at 70% 30%,#ffffff 0%,#e7eaee 40%,#c9ced5 100%)}

.step{top:666px;width:239px;height:165px;border-radius:6px;display:flex;flex-direction:column;align-items:center;justify-content:flex-end;padding-bottom:40px;color:var(--white);font-size:21px}
.step.red{background:var(--red-deep)}
.step.dark{background:var(--charcoal)}
.step svg{position:absolute;top:22px;left:50%;transform:translateX(-50%)}
.num{top:806px;width:46px;height:46px;border-radius:50%;background:var(--white);border:3px solid var(--charcoal);display:flex;align-items:center;justify-content:center;font-size:20px;color:var(--black)}
.num.r{border-color:var(--red-deep)}

.about-img{left:77px;top:917px;width:345px;height:207px;background:linear-gradient(180deg,#6d7784,#3f4650 55%,#8a6e4e)}
.about-title{left:477px;top:912px;font-family:"Exo 2",sans-serif;font-size:41px;color:var(--red-deep)}
.about-text{left:477px;top:970px;width:640px;font-size:14.3px;line-height:19.8px;color:#222}

/* services */
.services{left:0;top:1182px;width:1200px;height:468px;background:var(--black)}
.services-title{left:0;top:1228px;width:1200px;text-align:center;font-family:"Exo 2",sans-serif;font-size:40px;color:var(--white)}
.svc-img{top:1314px;width:333px;height:187px}
.svc-label{top:1522px;width:333px;text-align:center;color:var(--white);font-size:22px;letter-spacing:.5px}
.svc-desc{top:1556px;width:333px;text-align:center;color:var(--white);font-size:14px;line-height:19px}

/* story */
.story{left:0;top:1650px;width:1200px;height:367px;background:linear-gradient(180deg,#dfe7ee 0%,#f4f6f8 40%,#d8dde2 100%)}
.story-title{left:79px;top:1700px;font-family:"Exo 2",sans-serif;font-size:40px;color:var(--red-deep)}
.story-sub{left:80px;top:1757px;font-size:15px;font-weight:700;color:#111}
.story-text{left:80px;width:770px;font-size:14.3px;line-height:19.6px;color:#222}
.signature{left:870px;top:1790px;width:210px;height:60px;background:linear-gradient(90deg,rgba(208,40,45,.12),rgba(208,40,45,.04));border-radius:4px}
.founder{left:875px;top:1872px;font-size:19px;font-weight:700;color:#111}
.founder-role{left:875px;top:1903px;font-size:16px;color:#222}

/* partners */
.partner-name{top:2050px;width:249px;height:46px;display:flex;align-items:center;justify-content:center;font-family:"Exo 2",sans-serif;font-weight:600;font-size:24px;color:#222}
.partner-img{top:2104px;width:249px;height:106px;background:linear-gradient(180deg,#8c949d,#4d545c)}
.zoom{width:30px;height:30px}

/* map */
.map{left:0;top:2271px;width:1200px;height:367px;background:linear-gradient(135deg,#e4e2dc,#d6dccd 45%,#e6e3dd)}
.contact-card{left:383px;top:2400px;width:432px;height:183px;background:rgba(255,255,255,.88);border-radius:4px}
.contact-row{left:415px;display:flex;align-items:center;gap:14px;font-size:15px;color:#222}

/* footer */
.footer{left:0;top:2638px;width:1200px;height:356px;background:var(--black)}
.foot-brand{left:77px;top:2700px;width:290px;font-family:"Exo 2",sans-serif;font-weight:600;font-size:34px;line-height:38px;color:var(--white);letter-spacing:1px}
.foot-phone{left:77px;top:2818px;display:flex;align-items:center;gap:12px;font-family:"Exo 2",sans-serif;font-weight:600;font-size:38px;color:var(--red)}
.social{top:2904px;width:50px;height:50px;border-radius:50%;background:var(--white)}
.social.red{background:var(--red)}
.col-title{top:2690px;font-family:"Exo 2",sans-serif;font-size:26px;color:var(--red)}
.quick{left:407px;font-size:14.5px;color:var(--white)}
.blog-thumb{left:572px;width:72px;height:72px;border-radius:50%;background:linear-gradient(135deg,#c9b9a3,#5a6b85);border:2px solid #fff}
.blog-text{left:662px;width:160px;font-size:14.5px;line-height:19px;color:var(--white)}
.blog-date{font-style:italic;font-size:13px;display:block}
.testi{left:862px;top:2733px;width:270px;font-size:14.5px;line-height:20px;color:var(--white)}
.client{left:862px;top:2842px;font-size:14px;color:var(--red);font-weight:700}
.arrow-btn{top:2892px;width:28px;height:28px;background:#555;display:flex;align-items:center;justify-content:center}
.bottombar{left:0;top:2994px;width:1200px;height:62px;background:var(--red-deep);display:flex;align-items:center;justify-content:center;color:var(--white);font-size:15px}
</style>
</head>
<body>

<!-- top bar -->
<div class="abs topbar"></div>
<div class="abs top-item" style="left:530px">
  <svg width="18" height="18" viewBox="0 0 24 24" fill="#fff"><path d="M6.6 10.8a15.1 15.1 0 0 0 6.6 6.6l2.2-2.2c.3-.3.7-.4 1-.2 1.1.4 2.3.6 3.6.6.6 0 1 .4 1 1V20c0 .6-.4 1-1 1A17 17 0 0 1 3 4c0-.6.4-1 1-1h3.5c.6 0 1 .4 1 1 0 1.3.2 2.5.6 3.6.1.3 0 .7-.2 1z"/></svg>
  <span>139271</span>
</div>
<div class="abs top-item" style="left:640px">
  <svg width="22" height="16" viewBox="0 0 24 18" fill="none" stroke="#fff" stroke-width="1.8"><rect x="1" y="1" width="22" height="16"/><path d="M1 1l11 9 11-9"/></svg>
  <span>service@varnoelectrical-example.com.au</span>
</div>
<div class="abs search"><span>Search.....</span>
  <svg width="16" height="16" viewBox="0 0 16 16" fill="none" stroke="#fff" stroke-width="2.2"><circle cx="6.5" cy="6.5" r="5"/><path d="M10.5 10.5L15 15"/></svg>
</div>

<!-- header -->
<div class="abs brand"><span class="mark"></span><span class="name">VARNO ELECTRICAL</span></div>
<div class="abs nav active" style="left:525px">HOME</div>
<div class="abs nav" style="left:693px">VARNO STORY</div>
<div class="abs nav" style="left:862px">OUR WORK</div>
<div class="abs nav" style="left:1016px">CONTACT US</div>

<!-- hero -->
<div class="abs hero" role="img" aria-label="Photo of an electrician in a hard hat working on a switchboard"></div>
<div class="abs bokeh"></div>

<div class="abs step red" style="left:77px">
  <svg width="64" height="64" viewBox="0 0 24 24" fill="#fff"><path d="M6.6 10.8a15.1 15.1 0 0 0 6.6 6.6l2.2-2.2c.3-.3.7-.4 1-.2 1.1.4 2.3.6 3.6.6.6 0 1 .4 1 1V20c0 .6-.4 1-1 1A17 17 0 0 1 3 4c0-.6.4-1 1-1h3.5c.6 0 1 .4 1 1 0 1.3.2 2.5.6 3.6.1.3 0 .7-.2 1z"/></svg>
  CALL US</div>
<div class="abs step dark" style="left:346px">
  <svg width="80" height="64" viewBox="0 0 40 24" fill="#fff"><path d="M20 2C11 2 4 12 4 12s7 10 16 10 16-10 16-10S29 2 20 2z"/><circle cx="20" cy="12" r="6" fill="#2b2b2b"/><circle cx="20" cy="12" r="3" fill="#fff"/></svg>
  SITE ASSESSMENT</div>
<div class="abs step red" style="left:615px">
  <svg width="64" height="64" viewBox="0 0 24 24" fill="none" stroke="#fff" stroke-width="2.4" stroke-linecap="round"><circle cx="8" cy="8" r="3.5"/><path d="M8 2v2M8 12v2M2 8h2M12 8h2M3.8 3.8l1.4 1.4M10.8 10.8l1.4 1.4M3.8 12.2l1.4-1.4M10.8 5.2l1.4-1.4M13 13l8 8M20 4l-6 6"/></svg>
  INSTALLATION</div>
<div class="abs step dark" style="left:882px">
  <svg width="64" height="64" viewBox="0 0 24 24" fill="#fff"><path d="M4 12c0-4 3.5-7 8-7h3l3-2v3.5c1.2.9 2 2.1 2.4 3.5H22v4h-1.7c-.5 1-1.3 1.9-2.3 2.5V20h-3v-2h-4v2H8v-3c-2.4-1.2-4-3.1-4-5z"/><circle cx="11" cy="2.5" r="1.8"/></svg>
  SAVINGS</div>
<div class="abs num r" style="left:174px">1</div>
<div class="abs num" style="left:443px">2</div>
<div class="abs num r" style="left:712px">3</div>
<div class="abs num" style="left:979px">4</div>

<!-- about -->
<div class="abs about-img" role="img" aria-label="Photo of a warehouse interior with overhead lighting"></div>
<h2 class="abs about-title">About Varno</h2>
<p class="abs about-text">Lorem Ipsum is simply dummy text of the printing and typesetting industry. Lorem Ipsum has been the industry's standard dummy text ever since the 1500s, when an unknown printer took a galley of type and scrambled it to make a type specimen book. It has survived not only five centuries, but also the leap into electronic typesetting, remaining essentially unchanged. It was popularised in the 1960s with the release of Letraset sheets containing Lorem Ipsum passages, and more recently with desktop publishing software like Aldus PageMaker including versions of Lorem Ipsum.</p>

<!-- services -->
<div class="abs services"></div>
<h2 class="abs services-title">Our Services</h2>
<div class="abs svc-img" style="left:77px;background:linear-gradient(135deg,#9fb3c8,#e0c35a 55%,#5f6e7d)" role="img" aria-label="Photo of an electrician on the phone near power lines"></div>
<div class="abs svc-img" style="left:434px;background:linear-gradient(180deg,#5a4a3c,#3a2e24 45%,#e9a12a 75%,#4a3a2c)" role="img" aria-label="Photo of hanging concrete pendant LED lights"></div>
<div class="abs svc-img" style="left:790px;background:linear-gradient(135deg,#e8e4dc,#8aa0c2 50%,#3a4f86)" role="img" aria-label="Photo of a solar installer showing a panel to a couple"></div>
<div class="abs svc-label" style="left:77px">ELECTRICAL</div>
<div class="abs svc-label" style="left:434px">LED LIGHTING</div>
<div class="abs svc-label" style="left:790px">SOLAR POWER</div>
<p class="abs svc-desc" style="left:77px">Lorem Ipsum is simply dummy text of the<br>printing and typesetting industry.</p>
<p class="abs svc-desc" style="left:434px">Lorem Ipsum is simply dummy text of the<br>printing and typesetting industry.</p>
<p class="abs svc-desc" style="left:790px">Lorem Ipsum is simply dummy text of the<br>printing and typesetting industry.</p>

<!-- story -->
<div class="abs story" role="img" aria-label="Faint background photo of rooftop solar panels"></div>
<h2 class="abs story-title">Varno Story</h2>
<p class="abs story-sub">Varno Electrical. REC #40517.</p>
<p class="abs story-text" style="top:1800px">Electrical and Energy Solutions are at the forefront of our company. Varno Electrical has a long history in Electrical, LED Lighting and Solar Power and just like the Cougar, we will strive to be fierce &amp; agile in an effort to exceed our customer's expectations and develop stronger links with all our business partners &amp; community.</p>
<p class="abs story-text" style="top:1870px">Varno Electrical is an expert Electrical Company providing services to all Residential and Commercial customers. With over 10 years of experience, Varno Electrical has developed a highly-experienced team of professionals that ensure all our customer expectations are exceeded. Our team comprise of over 70 staff of Designers, Consultants, Electricians who provide expert advice and quality of installation at an affordable price.</p>
<div class="abs signature" role="img" aria-label="Handwritten signature of the managing director"></div>
<p class="abs founder">Daniel Morrow</p>
<p class="abs founder-role">Managing Director &amp; Founder</p>

<!-- partners -->
<svg class="abs" style="left:24px;top:2110px" width="28" height="40" viewBox="0 0 28 40"><path d="M22 4L6 20l16 16" fill="none" stroke="#c0282d" stroke-width="6"/></svg>
<svg class="abs" style="left:1148px;top:2110px" width="28" height="40" viewBox="0 0 28 40"><path d="M6 4l16 16L6 36" fill="none" stroke="#222" stroke-width="6"/></svg>

<div class="abs partner-name" style="left:77px">Harlow Signs</div>
<div class="abs partner-name" style="left:342px">Steelmark</div>
<div class="abs partner-name" style="left:607px">Boardline</div>
<div class="abs partner-name" style="left:872px">Trailpack Stores</div>

<div class="abs partner-img" style="left:77px" role="img" aria-label="Photo of a completed warehouse lighting project"></div>
<div class="abs partner-img" style="left:342px" role="img" aria-label="Photo of a factory interior lighting project"></div>
<div class="abs partner-img" style="left:607px;background:linear-gradient(180deg,#9fb8d6,#e5e5e5 45%,#b83a3a)" role="img" aria-label="Photo of a building supplies storefront"></div>
<div class="abs partner-img" style="left:872px" role="img" aria-label="Photo of a retail store interior"></div>
<svg class="abs zoom" style="left:286px;top:2172px" viewBox="0 0 30 30" fill="none" stroke="#fff" stroke-width="3"><circle cx="12" cy="12" r="8"/><path d="M18 18l9 9M8 12h8M12 8v8"/></svg>
<svg class="abs zoom" style="left:551px;top:2172px" viewBox="0 0 30 30" fill="none" stroke="#fff" stroke-width="3"><circle cx="12" cy="12" r="8"/><path d="M18 18l9 9M8 12h8M12 8v8"/></svg>
<svg class="abs zoom" style="left:816px;top:2172px" viewBox="0 0 30 30" fill="none" stroke="#fff" stroke-width="3"><circle cx="12" cy="12" r="8"/><path d="M18 18l9 9M8 12h8M12 8v8"/></svg>
<svg class="abs zoom" style="left:1081px;top:2172px" viewBox="0 0 30 30" fill="none" stroke="#fff" stroke-width="3"><circle cx="12" cy="12" r="8"/><path d="M18 18l9 9M8 12h8M12 8v8"/></svg>

<!-- map -->
<div class="abs map" role="img" aria-label="Street map of the Glenbrook area showing the office location"></div>
<div class="abs contact-card"></div>
<div class="abs contact-row" style="top:2436px">
  <svg width="20" height="24" viewBox="0 0 20 24" fill="#d0282d"><path d="M10 0a8 8 0 0 0-8 8c0 6 8 16 8 16s8-10 8-16a8 8 0 0 0-8-8zm0 11a3 3 0 1 1 0-6 3 3 0 0 1 0 6z"/></svg>
  <span>12/48 Larkin St Glenbrook VIC 3150</span></div>
<div class="abs contact-row" style="top:2484px">
  <svg width="22" height="22" viewBox="0 0 24 24" fill="#d0282d"><path d="M6.6 10.8a15.1 15.1 0 0 0 6.6 6.6l2.2-2.2c.3-.3.7-.4 1-.2 1.1.4 2.3.6 3.6.6.6 0 1 .4 1 1V20c0 .6-.4 1-1 1A17 17 0 0 1 3 4c0-.6.4-1 1-1h3.5c.6 0 1 .4 1 1 0 1.3.2 2.5.6 3.6.1.3 0 .7-.2 1z"/></svg>
  <span>139271</span></div>
<div class="abs contact-row" style="top:2532px">
  <svg width="24" height="18" viewBox="0 0 24 18"><rect width="24" height="18" rx="2" fill="#d0282d"/><path d="M1 2l11 8 11-8" fill="none" stroke="#fff" stroke-width="1.8"/></svg>
  <span>service@varnoelectrical-example.com.au</span></div>

<!-- footer -->
<div class="abs footer"></div>
<div class="abs foot-brand">VARNO<br>ELECTRICAL</div>
<div class="abs foot-phone">
  <svg width="44" height="38" viewBox="0 0 44 38" fill="#fff"><path d="M4 10c4-8 32-8 36 0l-2 6h-8l-1-5c-4-1-10-1-14 0l-1 5H6zM10 18h24l6 18H4z"/><circle cx="22" cy="27" r="5" fill="#111"/></svg>
  <span>139271</span></div>
<div class="abs social red" style="left:77px"></div>
<div class="abs social" style="left:142px"></div>
<div class="abs social" style="left:205px"></div>

<h3 class="abs col-title" style="left:407px">Quick Link</h3>
<p class="abs quick" style="top:2734px">Electrical</p>
<p class="abs quick" style="top:2770px">Led Lighting</p>
<p class="abs quick" style="top:2807px">Solar power</p>
<p class="abs quick" style="top:2844px">Career</p>

<h3 class="abs col-title" style="left:572px">Blog post</h3>
<div class="abs blog-thumb" style="top:2738px" role="img" aria-label="Blog thumbnail photo of LED lighting"></div>
<div class="abs blog-thumb" style="top:2832px" role="img" aria-label="Blog thumbnail photo of a solar installation"></div>
<p class="abs blog-text" style="top:2738px">Lorem Ipsum is simply dummy text of the.<span class="blog-date">01 th Feb, 2017</span></p>
<p class="abs blog-text" style="top:2832px">Lorem Ipsum is simply dummy text of the,<span class="blog-date">01 th Feb, 2017</span></p>

<h3 class="abs col-title" style="left:862px">Client Testimonial</h3>
<p class="abs testi">Lorem Ipsum is simply dummy text of the printing and typesetting industry.Lorem Ipsum has been the industry's</p>
<p class="abs client">- Client Name</p>
<div class="abs arrow-btn" style="left:862px"><svg width="10" height="14" viewBox="0 0 10 14"><path d="M8 1L2 7l6 6" fill="none" stroke="#fff" stroke-width="2"/></svg></div>
<div class="abs arrow-btn" style="left:895px"><svg width="10" height="14" viewBox="0 0 10 14"><path d="M2 1l6 6-6 6" fill="none" stroke="#fff" stroke-width="2"/></svg></div>

<div class="abs bottombar">©&nbsp;<strong>VARNO ELECTRICAL</strong>&nbsp;- 2017. All Rights Reserved</div>

</body>
</html>
```